Redesign of luchtvoorraadpunt.nl – Clean, Trustworthy & User-Friendly Medical Equipment We...

PLEASE DO NOT CONTACT US OUTSIDE KRAVELPOINT.COM

We are looking for a talented and creative web designer to redesign the website www.luchtvoorraadpunt.nl, a Dutch online store specializing in medical oxygen concentrators and related products.

The current website is functional but outdated in terms of design, structure, and user experience. We want a fresh, modern, and trustworthy design that reflects the medical and professional nature of the business, while also being clear, accessible, and easy to navigate for a broad audience — including elderly users and people with limited technical skills.

About the Business:
Luchtvoorraadpunt.nl provides high-quality oxygen concentrators and accessories for both home and mobile use. The target audience includes individuals with respiratory conditions, healthcare professionals, and caregivers. Trust, clarity, and ease of use are key.

What We’re Looking For:
A clean and modern layout with a medical/professional feel
Strong focus on usability and accessibility
A design that works flawlessly on desktop and mobile (responsive)
Clear product presentation and easy-to-use navigation
Use of calming colors (e.g. white, light blue, grey tones) that reflect a medical/healthcare environment
Clear call-to-actions (e.g. “Vraag een offerte aan”, “Neem contact op”, etc.)
A design that builds trust and encourages inquiries or purchases

Pages We Need Designed:
Homepage
Product overview page (category)
Product detail page

Inspiration / Style Examples:
We’re looking for something in the style of:

Varnoth Healthcare
Bralto.nl
Welzijnsdepot.nl
Quenby (for clean layout and spacing)

Deliverables:
Full desktop and mobile designs (Figma, Adobe PS)
All source files and assets used (fonts, icons, images, etc.)
Clean and organized layers
Design must be ready for implementation by our development team

Target Market(s)

Luchtvoorraadpunt.nl targets both B2C and B2B audiences within the medical and healthcare sector in europe

Industry/Entity Type

Medical

Number of Pages Required

2 page

Font styles to use
Sans Serif

Requirements
Must have
• Clean and professional design, responsive layout (desktop and mobile), calming medical color scheme (e.g. light blue, white, grey), clear product presentation with specs and images, strong call-to-actions (e.g. "Vraag een offerte aan"), trust elements (certifications, reviews, support info), easy navigation for elderly and non-tech-savvy users, contact form easily accessible, SEO-friendly structure, fast loading design, privacy and regulatory compliance elements (e.g. CE mark info, medical disclaimers).
Should not have
• Overly complex design, dark or aggressive color schemes, small or hard-to-read fonts, cluttered layout, distracting animations, unnecessary pop-ups, autoplay videos or sounds, technical jargon without explanation, hidden contact options, slow-loading pages.

```html
<!DOCTYPE html>
<html lang="en">
<head>
<meta charset="utf-8">
<title>Aerivo – Oxygen Concentrators</title>
<link href="https://fonts.googleapis.com/css2?family=Montserrat:wght@400;500;600;700;800&display=swap" rel="stylesheet">
<style>
:root{
  --primary:#3138d6;
  --sky:#2fa4f3;
  --navy:#141a4c;
  --ink:#33384a;
  --muted:#6b7080;
  --footer:#2f3542;
  --footer-dark:#2a2f3b;
  --white:#ffffff;
}
*{box-sizing:border-box;margin:0;padding:0}
html,body{width:1200px;height:4208px;overflow:hidden;background:var(--white)}
body{font-family:"Montserrat",sans-serif;color:var(--ink);position:relative}
.abs{position:absolute}
a{color:inherit;text-decoration:none}

.header{left:0;top:0;width:1200px;height:85px;background:var(--white)}
.brand{left:91px;top:20px;display:flex;align-items:center;gap:10px;font-weight:800;font-size:36px;color:var(--primary);letter-spacing:-.5px}
.brand-dot{width:14px;height:14px;border-radius:50%;background:var(--sky)}
.search{left:425px;top:26px;width:364px;height:34px;display:flex;border-radius:6px;overflow:hidden}
.search-field{flex:1;background:#eef0f4;font-size:10px;color:#9aa0ad;padding:11px 20px}
.search-btn{width:104px;background:var(--sky);color:#fff;font-size:10px;font-weight:700;display:flex;align-items:center;justify-content:center}
.tools{left:818px;top:30px;display:flex;align-items:center;gap:16px;font-size:10px;color:var(--ink)}
.tools svg{width:16px;height:16px;stroke:#555a6b;fill:none;stroke-width:1.6}
.cart{left:1028px;top:26px;display:flex;align-items:center;gap:10px}
.cart-icon{width:34px;height:34px;border-radius:6px;background:var(--sky);display:flex;align-items:center;justify-content:center}
.cart-text{font-size:8px;color:var(--muted);line-height:1.2}
.cart-text b{display:block;font-size:12px;color:var(--ink);font-weight:700}

.hero{left:0;top:85px;width:1200px;height:728px;background:linear-gradient(90deg,#1c1f45 0%,#2a2c4e 40%,#5a5060 70%,#3e3a48 100%)}
.hero-shade{left:0;top:85px;width:1200px;height:728px;background:linear-gradient(90deg,rgba(18,20,60,.85) 0%,rgba(25,28,70,.55) 45%,rgba(0,0,0,0) 75%)}
.nav{left:171px;top:85px;width:858px;height:55px;background:var(--primary);border-radius:0 0 8px 8px;display:flex;align-items:center;justify-content:center;gap:32px;color:#fff;font-size:14px;font-weight:500}
.hero-title{left:90px;top:348px;color:#fff;font-size:39px;font-weight:700;line-height:1.12;letter-spacing:-.3px}
.hero-sub{left:90px;top:455px;width:480px;color:#e6e8f4;font-size:12.5px;line-height:1.7}
.btn{display:inline-flex;align-items:center;justify-content:center;font-size:12px;font-weight:700;border-radius:6px;color:#fff;text-transform:uppercase}
.btn-sky{background:var(--sky)}
.hero-btn1{left:90px;top:523px;width:234px;height:44px}
.hero-btn2{left:333px;top:523px;width:182px;height:44px;border:1.5px solid #fff}
.callbox{left:921px;top:748px;width:279px;height:101px;background:var(--sky);border-radius:10px 0 0 10px;display:flex;align-items:center;gap:18px;padding-left:24px;color:#fff}
.call-ic{width:62px;height:62px;border-radius:8px;background:#fff;display:flex;align-items:center;justify-content:center}
.call-txt{font-size:15px;line-height:1.3}
.call-txt b{display:block;font-size:16px;font-weight:700}

.feature{top:915px;display:flex;align-items:center;gap:16px}
.feat-ic{width:64px;height:64px;border-radius:8px;background:#e5e7f9;display:flex;align-items:center;justify-content:center}
.feat-ic svg{width:34px;height:34px;stroke:var(--primary);fill:none;stroke-width:1.5}
.feat-t{font-size:14px;font-weight:700;color:var(--ink)}
.feat-s{font-size:11px;color:var(--muted);margin-top:6px}

.photo{border-radius:28px}
.about-img1{left:113px;top:1065px;width:405px;height:467px;background:linear-gradient(160deg,#b7b8bd,#8f8a86 55%,#4c4238)}
.about-img2{left:585px;top:1393px;width:501px;height:304px;background:linear-gradient(120deg,#caa78a,#e5d8cc 50%,#6f6258)}
.sec-title{font-size:29px;font-weight:600;color:#3a3d4c}
.about-title{left:585px;top:1128px}
.body-text{font-size:11.5px;line-height:1.8;color:var(--muted)}
.about-text{left:585px;top:1183px;width:430px}
.about-text p+p{margin-top:12px}

.best{left:59px;top:1793px;width:1084px;height:537px;border:1.5px solid #aeb2ee;border-radius:64px;background:linear-gradient(180deg,#eef0fc,#e7e9fa)}
.best-title{left:0;top:1868px;width:1200px;text-align:center}
.card{top:1947px;width:227px;height:264px;background:#fff;border:1.5px solid #aac4f0;border-radius:14px;padding:9px}
.card-img{height:150px;border-radius:10px;background:#eeeeef}
.card-name{font-size:12px;font-weight:500;color:#2e3140;text-transform:uppercase;line-height:1.5;margin:22px 16px 4px}
.card-price{font-size:12px;font-weight:700;color:var(--primary);margin-left:16px}
.card.active{background:var(--sky);border-color:var(--sky);height:295px}
.card.active .card-img{background:#fff}
.card.active .card-name,.card.active .card-price{color:#fff}
.qty{position:absolute;right:26px;top:223px;width:30px;height:18px;border-radius:9px;background:rgba(255,255,255,.35);color:#fff;font-size:10px;display:flex;align-items:center;justify-content:center}
.add{font-size:10.5px;font-weight:700;color:#fff;text-decoration:underline;margin:12px 16px}

.comp-title{left:144px;top:2530px;line-height:1.5}
.comp-text{left:144px;top:2635px;width:410px}
.comp-img{left:647px;top:2440px;width:403px;height:403px;background:linear-gradient(150deg,#cfd0d4,#7c7570 50%,#3b3a40)}

.feat-title{left:0;top:2915px;width:1200px;text-align:center}
.banner-under{left:163px;top:3380px;width:874px;height:71px;background:var(--sky);border-radius:0 0 60px 60px}
.banner{left:59px;top:2980px;width:1084px;height:440px;border-radius:70px;background:linear-gradient(90deg,#3a3d55 0%,#20244f 35%,#141a5a 60%,#121763 100%);overflow:hidden}
.ban-title{left:596px;top:3070px;color:#fff;font-size:24px;font-weight:700}
.ban-text{left:596px;top:3118px;width:440px;color:#d9dcf3;font-size:11.5px;line-height:1.8}
.ban-list{left:596px;top:3192px;list-style:none;color:#e4e6f6;font-size:11.5px}
.ban-list li{margin-bottom:12px;display:flex;align-items:center;gap:8px}
.ban-list li::before{content:"";width:4px;height:4px;border-radius:50%;background:var(--sky)}
.ban-btn{left:597px;top:3292px;width:133px;height:42px}

.brand-title{left:0;top:3533px;width:1200px;text-align:center}
.all-brands{left:899px;top:3548px;font-size:12px;font-weight:600;color:#3a3d4c;text-decoration:underline}
.brand-tile{top:3599px;width:172px;height:56px;border-radius:6px;border:1.5px solid #b9c8ef;display:flex;align-items:center;justify-content:center;font-size:18px;font-weight:700;color:var(--navy)}

.footer{left:0;top:3754px;width:1200px;height:402px;background:var(--footer)}
.foot-col{top:3868px}
.foot-col h4{color:#fff;font-size:15px;font-weight:700;margin-bottom:24px}
.foot-col li{list-style:none;color:#d7dae3;font-size:12.5px;margin-bottom:12px}
.foot-div{top:3868px;width:1px;height:220px;background:#3f4553}
.news{left:874px;top:3948px;width:212px;height:40px;border-radius:6px;background:#3b4150;display:flex;align-items:center;padding:0 14px;gap:8px;color:#e6e8ef;font-size:11px}
.bottom{left:0;top:4156px;width:1200px;height:52px;background:var(--footer-dark);color:#d7dae3;font-size:12.5px;display:flex;align-items:center;justify-content:center}
</style>
</head>
<body>

<header class="abs header">
  <div class="abs brand"><span class="brand-dot"></span>Aerivo</div>
  <div class="abs search"><div class="search-field">Search here...</div><div class="search-btn">SEARCH</div></div>
  <div class="abs tools">
    <span>🌐 Eng ⌄</span>
    <svg viewBox="0 0 16 16"><circle cx="8" cy="5" r="3"/><path d="M2 15c0-3.5 2.7-5 6-5s6 1.5 6 5"/></svg>
    <svg viewBox="0 0 16 16"><rect x="3" y="2" width="10" height="12" rx="1"/><path d="M5 6h6M5 9h6"/></svg>
    <svg viewBox="0 0 16 16"><path d="M8 14S2 10 2 5.5A3 3 0 0 1 8 4a3 3 0 0 1 6 1.5C14 10 8 14 8 14z"/></svg>
    <svg viewBox="0 0 16 16"><path d="M2 5h11l-3-3M14 11H3l3 3"/></svg>
  </div>
  <div class="abs cart">
    <div class="cart-icon"><svg width="18" height="18" viewBox="0 0 18 18" fill="none" stroke="#fff" stroke-width="1.8"><path d="M1 2h3l2 9h9l2-7H5"/><circle cx="7" cy="15" r="1.3"/><circle cx="14" cy="15" r="1.3"/></svg></div>
    <div class="cart-text">0 item(s)<b>€0.00</b></div>
  </div>
</header>

<div class="abs hero" role="img" aria-label="Photo of a man wearing an oxygen mask while talking on a phone"></div>
<div class="abs hero-shade"></div>
<nav class="abs nav"><span>All categories ⌄</span><span>Oxygen concentrator ⌄</span><span>Portable Oxygen concentrator ⌄</span><span>Filters</span><span>Rental</span><span>Supplies</span></nav>
<h1 class="abs hero-title">Breathe Easier with<br>Trusted Oxygen Solutions</h1>
<p class="abs hero-sub">High-quality oxygen concentrators for home and travel use — safe, reliable, and recommended by healthcare professionals.</p>
<a class="abs btn btn-sky hero-btn1">View all concentrators</a>
<a class="abs btn hero-btn2">Get expert advice</a>
<div class="abs callbox">
  <div class="call-ic"><svg width="28" height="28" viewBox="0 0 24 24" fill="#2f3542"><path d="M6.6 10.8a15 15 0 0 0 6.6 6.6l2.2-2.2c.3-.3.7-.4 1-.2 1.1.4 2.3.6 3.6.6.6 0 1 .4 1 1V20c0 .6-.4 1-1 1A17 17 0 0 1 3 4c0-.6.4-1 1-1h3.5c.6 0 1 .4 1 1 0 1.3.2 2.5.6 3.6.1.3 0 .7-.2 1z"/></svg></div>
  <div class="call-txt">Call Us<b>0031-705550142</b></div>
</div>

<section>
  <div class="abs feature" style="left:69px">
    <div class="feat-ic"><svg viewBox="0 0 34 34"><rect x="3" y="10" width="18" height="13"/><path d="M21 14h6l4 5v4H21"/><circle cx="9" cy="25" r="2.5"/><circle cx="26" cy="25" r="2.5"/></svg></div>
    <div><div class="feat-t">Free Shipping</div><div class="feat-s">above € 250 in the EU</div></div>
  </div>
  <div class="abs feature" style="left:335px">
    <div class="feat-ic"><svg viewBox="0 0 34 34"><rect x="11" y="9" width="12" height="20" rx="3"/><path d="M14 9V5h6v4M14 15h6M14 19h6"/></svg></div>
    <div><div class="feat-t">Oxygen concentrator</div><div class="feat-s">Oxygen concentrator for travel</div></div>
  </div>
  <div class="abs feature" style="left:645px">
    <div class="feat-ic"><svg viewBox="0 0 34 34"><rect x="9" y="4" width="16" height="26" rx="2"/><circle cx="17" cy="14" r="4"/><path d="M13 23h8"/></svg></div>
    <div><div class="feat-t">Secure Shopping</div><div class="feat-s">Best security features</div></div>
  </div>
  <div class="abs feature" style="left:913px">
    <div class="feat-ic"><svg viewBox="0 0 34 34"><circle cx="17" cy="17" r="11"/><circle cx="17" cy="14" r="3"/><path d="M11 24c1-4 11-4 12 0"/></svg></div>
    <div><div class="feat-t">22 years<br>experience</div></div>
  </div>
</section>

<section>
  <div class="abs photo about-img1" role="img" aria-label="Photo of a young woman using an oxygen mask at a laptop"></div>
  <h2 class="abs sec-title about-title">About oxygen</h2>
  <div class="abs body-text about-text">
    <p>As business and consumer you want the best equipment for the sharpest prices. We offer the best stationary oxygen concentrators, portable oxygen concentrators, accessories and disposables. Compare and make the best choice for you and your business.</p>
    <p>Aerivo BV more than 22 years experience your partner for innovative technology and service. With our online shop we keep you constantly informed of the various systems. Questions or wishes? Don't hesitate to contact us.</p>
  </div>
  <div class="abs photo about-img2" role="img" aria-label="Photo of a girl in a chair breathing through an oxygen mask"></div>
</section>

<section>
  <div class="abs best"></div>
  <h2 class="abs sec-title best-title">Best-Selling Products</h2>
  <div class="abs card" style="left:127px"><div class="card-img" role="img" aria-label="Product photo of a nasal cannula"></div><div class="card-name">Cannula Nasoflow Soft 2.1 meter Medivane</div><div class="card-price">€1.79</div></div>
  <div class="abs card" style="left:367px"><div class="card-img" role="img" aria-label="Product photo of a white oxygen concentrator"></div><div class="card-name">Orbis CX-4 oxygen concentrator</div><div class="card-price">€625.00</div></div>
  <div class="abs card active" style="left:607px"><div class="card-img" role="img" aria-label="Product photo of a portable oxygen concentrator with carry bag"></div><div class="card-name">Lumen 5 oxygen concentrator</div><div class="card-price">€999.00</div><div class="qty">1</div><div class="add">ADD TO CART</div></div>
  <div class="abs card" style="left:846px"><div class="card-img" role="img" aria-label="Product photo of a 10 liter oxygen concentrator"></div><div class="card-name">Kestra 10 liter oxygen concentrator</div><div class="card-price">€1,084.55</div></div>
</section>

<section>
  <h2 class="abs sec-title comp-title">Aerivo BV<br>Oxygen Concentrator</h2>
  <p class="abs body-text comp-text">Aerivo BV was founded in 2003 and has a premium range of oxygen concentrators. We have the largest online offers for the Netherlands and Belgium. Whether you are looking for a fixed oxygen concentrator or a portable / mobile oxygen concentrator. We make the difference in knowledge, service and low prices.</p>
  <div class="abs photo comp-img" role="img" aria-label="Photo of a woman seated on a bed using an oxygen mask"></div>
</section>

<section>
  <h2 class="abs sec-title feat-title">Featured Categories</h2>
  <div class="abs banner-under"></div>
  <div class="abs banner" role="img" aria-label="Photo of a man wearing an oxygen mask on a dark blue background"></div>
  <h3 class="abs ban-title">Portable Oxygen Concentrators</h3>
  <p class="abs ban-text">Lightweight and compact concentrators designed for daily mobility and travel. Long-lasting battery ensures freedom wherever you go. Ideal for active users who need reliable oxygen support.</p>
  <ul class="abs ban-list"><li>Easy to carry and travel-friendly</li><li>Long battery life for all-day use</li><li>Quiet operation suitable for public spaces</li></ul>
  <a class="abs btn btn-sky ban-btn">Shop now</a>
</section>

<section>
  <h2 class="abs sec-title brand-title">Shop by Brand</h2>
  <a class="abs all-brands">ALL MANUFACTURERS</a>
  <div class="abs brand-tile" style="left:150px;background:#dde5f6">Velaris</div>
  <div class="abs brand-tile" style="left:331px">Nasoflow</div>
  <div class="abs brand-tile" style="left:514px;background:#fdf6e6">Corvent</div>
  <div class="abs brand-tile" style="left:697px">Pneumi</div>
  <div class="abs brand-tile" style="left:878px;background:#f1f1f3">Halden Resp</div>
</section>

<footer>
  <div class="abs footer"></div>
  <div class="abs foot-col" style="left:114px"><h4>About Us</h4><ul><li>About Us</li><li>Delivery</li><li>Privacy Policy</li><li>Terms &amp; Conditions</li><li>Business</li></ul></div>
  <div class="abs foot-div" style="left:293px"></div>
  <div class="abs foot-col" style="left:343px"><h4>Customer Service</h4><ul><li>Contact</li><li>Warranty and Service</li><li>Returns</li><li>Site Map</li><li>Brands</li></ul></div>
  <div class="abs foot-div" style="left:542px"></div>
  <div class="abs foot-col" style="left:593px"><h4>My Account</h4><ul><li>My Account</li><li>Order History</li></ul><h4 style="margin-top:20px">Documentation</h4><ul><li>Frequently asked questions</li></ul></div>
  <div class="abs foot-div" style="left:824px"></div>
  <div class="abs foot-col" style="left:874px"><h4>Follow Us</h4><ul><li>Subscribe Our Newsletter for<br>latest News</li></ul></div>
  <div class="abs news"><svg width="12" height="10" viewBox="0 0 12 10" fill="none" stroke="#2fa4f3" stroke-width="1.4"><rect x="1" y="1" width="10" height="8"/><path d="M1 1l5 4 5-4"/></svg><span style="flex:1">Enter your email...</span><svg width="14" height="14" viewBox="0 0 14 14" fill="#2fa4f3"><path d="M1 7l12-6-4 12-2-5z"/></svg></div>
  <div class="abs bottom">Copyright ©2025, Aerivo BV, All Rights Reserved</div>
</footer>

</body>
</html>
```